Brivolt Technologies business card design

We need a business card designed with our new logo. it would be great if the card could communicate it is a technology based company.

Target Market(s)

system integrators

Industry/Entity Type

technology, IOT

Contact Information for Business Card

Name, designation, Address, telephone number, email address

Requirements
Must have
• logo and company name
Nice to have
• something to do with technology

```html
<!DOCTYPE html>
<html lang="en">
<head>
<meta charset="utf-8">
<title>Brivolt Technologies – Business Card</title>
<link rel="stylesheet" href="https://fonts.googleapis.com/css2?family=Exo+2:wght@600;700&family=Roboto:wght@400&display=swap">
<style>
  :root {
    --backdrop: #e9e6e1;
    --charcoal: #3e3e41;
    --ink: #2f3033;
    --orange: #f7931e;
    --silver: #bdbdc0;
    --paper: #ffffff;
    --text: #3a3a3d;
  }
  * { margin: 0; padding: 0; box-sizing: border-box; }
  html, body { width: 900px; height: 1200px; overflow: hidden; background: var(--backdrop); }
  .canvas { position: relative; width: 900px; height: 1200px; }

  .card {
    position: absolute;
    left: 86px;
    width: 735px;
    height: 431px;
    border-radius: 24px;
    overflow: hidden;
    box-shadow: 0 6px 14px rgba(0,0,0,0.22);
  }
  .card--front { top: 136px; background: var(--charcoal); display: flex; align-items: center; justify-content: center; }
  .card--back { top: 633px; background: var(--paper); }

  .brand { display: flex; align-items: center; gap: 14px; }
  .brand__mark { width: 18px; height: 18px; flex: none; }
  .brand__name {
    font-family: "Exo 2", sans-serif;
    font-weight: 700;
    letter-spacing: 1px;
    text-transform: uppercase;
    white-space: nowrap;
  }
  .card--front .brand__mark { background: #1d1d1f; }
  .card--front .brand__name { color: var(--silver); font-size: 40px; }

  .card--back .brand { position: absolute; left: 37px; top: 84px; }
  .card--back .brand__mark { background: var(--orange); }
  .card--back .brand__name { color: var(--ink); font-size: 32px; }

  .person { position: absolute; left: 145px; top: 210px; }
  .person__name {
    font-family: "Exo 2", sans-serif;
    font-weight: 700;
    font-size: 28px;
    line-height: 34px;
    color: var(--orange);
  }
  .person__role {
    font-family: "Roboto", sans-serif;
    font-size: 18px;
    line-height: 24px;
    color: var(--text);
  }

  .contacts { position: absolute; left: 145px; top: 314px; list-style: none; }
  .contacts li {
    display: flex; align-items: center; gap: 11px;
    font-family: "Roboto", sans-serif;
    font-size: 18px; line-height: 25.5px;
    color: var(--text);
    letter-spacing: 0.3px;
  }
  .contacts svg { width: 13px; height: 13px; flex: none; fill: var(--orange); }

  .address {
    position: absolute; left: 491px; top: 340px;
    font-family: "Roboto", sans-serif;
    font-size: 18px; line-height: 26px;
    color: var(--text);
    letter-spacing: 0.3px;
  }

  .footer-band { position: absolute; left: 0; bottom: 0; width: 100%; height: 14px; }
  .footer-band__accent { position: absolute; left: 0; top: 0; width: 134px; height: 14px; background: var(--orange); }
  .footer-band__main { position: absolute; left: 144px; right: 0; top: 0; height: 14px; background: var(--charcoal); }
</style>
</head>
<body>
<main class="canvas">
  <section class="card card--front" aria-label="Card front">
    <div class="brand">
      <span class="brand__mark"></span>
      <span class="brand__name">Brivolt Technologies</span>
    </div>
  </section>

  <section class="card card--back" aria-label="Card back">
    <div class="brand">
      <span class="brand__mark"></span>
      <span class="brand__name">Brivolt Technologies</span>
    </div>

    <div class="person">
      <h1 class="person__name">Marlow Penhale</h1>
      <p class="person__role">Managing Director</p>
    </div>

    <ul class="contacts">
      <li>
        <svg viewBox="0 0 24 24" aria-hidden="true"><path d="M6.6 10.8a15.1 15.1 0 0 0 6.6 6.6l2.2-2.2a1 1 0 0 1 1-.25 11.4 11.4 0 0 0 3.6.57 1 1 0 0 1 1 1V20a1 1 0 0 1-1 1A17 17 0 0 1 3 4a1 1 0 0 1 1-1h3.5a1 1 0 0 1 1 1c0 1.25.2 2.45.57 3.57a1 1 0 0 1-.25 1z"/></svg>
        +1 000 000 0000
      </li>
      <li>
        <svg viewBox="0 0 24 24" aria-hidden="true"><path d="M2 5h20v2.2l-10 6-10-6zM2 9.5l10 6 10-6V19H2z"/></svg>
        m_penhale@brivoltmail.com
      </li>
      <li>
        <svg viewBox="0 0 24 24" aria-hidden="true"><path d="M12 2a10 10 0 1 0 0 20 10 10 0 0 0 0-20zm6.9 9h-3a15 15 0 0 0-1.3-5.9A8 8 0 0 1 18.9 11zM12 4.1c.9 1.2 1.8 3.6 2 6.9h-4c.2-3.3 1.1-5.7 2-6.9zM9.4 5.1A15 15 0 0 0 8.1 11h-3a8 8 0 0 1 4.3-5.9zM5.1 13h3a15 15 0 0 0 1.3 5.9A8 8 0 0 1 5.1 13zm6.9 6.9c-.9-1.2-1.8-3.6-2-6.9h4c-.2 3.3-1.1 5.7-2 6.9zm2.6-1a15 15 0 0 0 1.3-5.9h3a8 8 0 0 1-4.3 5.9z"/></svg>
        www.brivolt-tech.com
      </li>
    </ul>

    <address class="address" style="font-style: normal;">
      48 Harrow Lane, Suite B<br>
      London, UK N4 7QT
    </address>

    <div class="footer-band" aria-hidden="true">
      <span class="footer-band__accent"></span>
      <span class="footer-band__main"></span>
    </div>
  </section>
</main>
</body>
</html>
```